Hollow Thicket, a 3d voxel survival video game needs a card for gaming conventions

I am the lead developer for Hollow Thicket http://www.HollowThicket.example and need a business card to hand out at an indie gaming convention
The card would need to include the game name, website url, my name, position (Lead Developer), e-mail and phone number
The game is a 3d, voxel (with smooth terrain) based survival game with guns and wildlife. The main icon of the game would likely be a grizzly bear but I am willing to accept other designs too.
Attached is a media kit for the game with some images you can use but don't have to its just what little art I can provide. Anything on the website or from the video game can also be used. unrelated art can also be used.
Target Market(s)
Indie Developers/publishers at conferences
Industry/Entity Type
Games
Contact Information for Business Card
Name: Corin Waldrick
Position: Lead Developer
E-mail: Pale_Kettle@mailbox.example
Phone number: 555-372-1186

```html
<!DOCTYPE html>
<html lang="en">
<head>
<meta charset="utf-8">
<title>Hollow Thicket — Business Card</title>
<link href="https://fonts.googleapis.com/css2?family=Source+Sans+3:wght@400;600;800&display=swap" rel="stylesheet">
<style>
  :root {
    --stage: #000000;
    --card-top: #a3170b;
    --card-mid: #a5452a;
    --card-bottom: #ab9158;
    --ink: #1a0d08;
    --brand: #7a150c;
    --fur-light: #8a5a33;
    --fur-dark: #3e2614;
    --envelope-fold: #a98a55;
  }
  * { margin: 0; padding: 0; box-sizing: border-box; }
  html, body {
    width: 1200px; height: 900px; overflow: hidden;
    background: var(--stage);
    font-family: "Source Sans 3", sans-serif;
  }
  .stage { position: relative; width: 1200px; height: 900px; }
  .card {
    position: absolute; top: 276px; width: 477px; height: 293px;
    overflow: hidden;
    background: linear-gradient(180deg, var(--card-top) 0%, var(--card-mid) 50%, var(--card-bottom) 100%);
  }
  .card--front { left: 116px; border-radius: 0 50px 0 50px; }
  .card--back { left: 622px; border-radius: 50px 0 50px 0; }

  .brand-mark {
    position: absolute; color: var(--brand);
    font-weight: 800; text-transform: uppercase; letter-spacing: 2px; line-height: 1;
    white-space: nowrap;
  }
  .brand-mark span { display: block; }
  .card--front .brand-mark { left: 30px; top: 34px; font-size: 30px; }
  .card--front .brand-mark span + span { margin-left: 34px; margin-top: 4px; }
  .card--back .brand-mark { left: 166px; top: 156px; font-size: 44px; }
  .card--back .brand-mark span + span { margin-left: 48px; margin-top: 6px; }

  .holder { position: absolute; left: 29px; top: 147px; color: var(--ink); }
  .holder__name { font-size: 17px; font-weight: 600; line-height: 1.2; }
  .holder__role { font-size: 13px; line-height: 1.2; margin-top: 1px; }

  .contact { position: absolute; left: 29px; top: 210px; list-style: none; color: var(--ink); font-size: 13px; }
  .contact li { display: flex; align-items: center; gap: 7px; height: 17px; white-space: nowrap; }
  .contact svg { width: 11px; height: 11px; fill: var(--ink); flex: none; }

  .mascot-photo {
    position: absolute;
    background: radial-gradient(ellipse at 40% 35%, var(--fur-light) 0%, var(--fur-dark) 80%);
  }
  .card--front .mascot-photo { left: 258px; top: 16px; width: 219px; height: 277px; border-radius: 46% 40% 0 20% / 30% 30% 0 20%; }
  .card--back .mascot-photo { left: 0; top: 54px; width: 162px; height: 239px; border-radius: 0 60% 0 0 / 0 40% 0 0; }
</style>
</head>
<body>
<main class="stage">
  <section class="card card--front">
    <div class="brand-mark"><span>Hollow</span><span>Thicket</span></div>
    <div class="mascot-photo" role="img" aria-label="Photograph of a roaring grizzly bear, front half"></div>
    <div class="holder">
      <p class="holder__name">Corin Waldrick</p>
      <p class="holder__role">Lead Developer</p>
    </div>
    <ul class="contact">
      <li><svg viewBox="0 0 24 24" aria-hidden="true"><path d="M6.6 10.8a15.1 15.1 0 0 0 6.6 6.6l2.2-2.2a1 1 0 0 1 1-.25 11.4 11.4 0 0 0 3.6.57 1 1 0 0 1 1 1V20a1 1 0 0 1-1 1A17 17 0 0 1 3 4a1 1 0 0 1 1-1h3.5a1 1 0 0 1 1 1c0 1.25.2 2.45.57 3.57a1 1 0 0 1-.25 1z"/></svg>555-372-1186</li>
      <li><svg viewBox="0 0 24 24" aria-hidden="true"><path d="M2 5h20v14H2z"/><path d="M3 6l9 6 9-6" stroke="var(--envelope-fold)" stroke-width="2" fill="none"/></svg>Pale_Kettle@mailbox.example</li>
      <li><svg viewBox="0 0 24 24" aria-hidden="true"><circle cx="12" cy="12" r="9" fill="none" stroke="var(--ink)" stroke-width="2.5"/><path d="M3 12h18M12 3c-3 3-3 15 0 18M12 3c3 3 3 15 0 18" fill="none" stroke="var(--ink)" stroke-width="2"/></svg>www.HollowThicket.example</li>
    </ul>
  </section>

  <section class="card card--back">
    <div class="mascot-photo" role="img" aria-label="Photograph of a grizzly bear, rear half, standing in grass"></div>
    <div class="brand-mark"><span>Hollow</span><span>Thicket</span></div>
  </section>
</main>
</body>
</html>
```